Coral Bay Pools New website

I currently operate a swimming pool service and repair business and looking for a re design for my website as it has been over 5 years since it was designed. current site is coralbaypoolslv.com

```html
<!DOCTYPE html>
<html lang="en">
<head>
<meta charset="utf-8">
<title>Coral Bay Pools LV</title>
<link href="https://fonts.googleapis.com/css2?family=Playfair+Display:wght@600;700&family=Poppins:wght@400;500;600;700&display=swap" rel="stylesheet">
<style>
  :root{
    --backdrop:#cfcfcf;
    --pool-blue:#0e6db0;
    --deep-blue:#0a5797;
    --sky-blue:#3bb4e8;
    --orange:#f7941d;
    --band-orange:#fb8a0c;
    --gold:#f6aa1c;
    --white:#ffffff;
    --footer-text:#555555;
    --serif:'Playfair Display', Georgia, serif;
    --sans:'Poppins', Arial, sans-serif;
  }
  *{box-sizing:border-box;margin:0;padding:0}
  html,body{width:1200px;height:2445px;overflow:hidden;background:var(--backdrop)}
  .stage{width:1264px;height:2576px;transform:scale(0.949367);transform-origin:0 0;position:relative}
  .page{position:absolute;left:85px;top:85px;width:1093px;height:2405px;background:var(--pool-blue);overflow:hidden;box-shadow:0 4px 14px rgba(0,0,0,.18);font-family:var(--sans);color:var(--white)}
  .abs{position:absolute}
  .deco{position:absolute;left:0;top:0;width:1093px;height:2405px;pointer-events:none}

  .nav{position:absolute;top:14px;right:25px;display:flex;gap:26px;font-weight:600;font-size:13px}
  .nav a{color:var(--white);text-decoration:none;position:relative}
  .nav a.active::after{content:"";position:absolute;left:0;right:0;bottom:-8px;height:2px;background:var(--orange)}

  .brand{position:absolute;left:157px;top:82px;width:240px;display:flex;align-items:center;justify-content:center;gap:10px;font-family:var(--sans);font-weight:700;font-size:22px;color:var(--white)}
  .brand-dot{width:18px;height:18px;border-radius:50%;background:var(--orange)}

  .hero-title{position:absolute;left:40px;width:475px;top:222px;text-align:center;font-family:var(--serif);font-weight:700;font-size:44px;line-height:51px;text-transform:uppercase}
  .hero-sub{position:absolute;left:40px;width:475px;top:388px;text-align:center;font-size:19px;line-height:34px}
  .btn{display:inline-flex;align-items:center;justify-content:center;background:var(--orange);color:var(--white);font-weight:700;text-transform:uppercase;border-radius:2px}
  .hero-btn{position:absolute;left:187px;top:477px;width:180px;height:39px;font-size:15px}

  .ring-word{position:absolute;left:0;width:1093px;display:flex;justify-content:center;font-family:var(--serif);font-weight:700;font-size:38px}
  .ring-word span{width:44px;height:44px;margin:0 -1.5px;border:2px solid var(--gold);border-radius:50%;display:flex;align-items:center;justify-content:center;line-height:1}

  .card{position:absolute;top:791px;width:224px;height:255px;border:1.5px solid var(--white);border-radius:6px;text-align:center}
  .card-icon{position:absolute;left:84px;top:42px;width:56px;height:56px;transform:rotate(45deg);background:var(--white);border:3px solid var(--gold);border-radius:6px;box-shadow:0 3px 6px rgba(0,0,0,.25)}
  .card-icon i{position:absolute;left:12px;top:12px;width:26px;height:26px;background:var(--deep-blue);border-radius:3px;display:block}
  .card h3{position:absolute;top:125px;left:0;right:0;font-family:var(--serif);font-weight:700;font-size:17px}
  .card p{position:absolute;top:151px;left:18px;right:18px;font-size:10px;line-height:15.5px}
  .card .btn{position:absolute;left:70px;top:210px;width:84px;height:22px;font-size:9px;border-radius:3px}

  .about-head{position:absolute;left:530px;width:490px;top:1133px;text-align:center;font-family:var(--serif);font-weight:700;line-height:44px}
  .about-head .small{font-size:34px;font-weight:600}
  .about-head .big{font-size:37px}
  .about-text{position:absolute;left:526px;width:498px;top:1233px;text-align:center;font-size:10.3px;line-height:17px}
  .about-btn{position:absolute;left:735px;top:1357px;width:83px;height:23px;font-size:9px;border-radius:3px}

  .band{position:absolute;left:0;top:1531px;width:1093px;height:244px;background:var(--band-orange);text-align:center}
  .band h2{position:absolute;left:0;right:0;top:30px;font-family:var(--serif);font-weight:700;font-size:46px}
  .band p{position:absolute;left:0;right:0;top:96px;font-size:24px}
  .band-btn{position:absolute;left:429px;top:149px;width:236px;height:52px;background:var(--deep-blue);color:var(--white);font-weight:700;font-size:21px;display:flex;align-items:center;justify-content:center;border-radius:2px}

  .contact-intro{position:absolute;left:0;width:1093px;top:1964px;text-align:center;font-size:16.5px;line-height:23px}
  .form{position:absolute;left:174px;top:2037px;width:353px;height:271px;border:1.5px solid rgba(255,255,255,.7);border-radius:10px}
  .field{position:absolute;left:19px;width:315px;height:26px;background:rgba(255,255,255,.12);border-radius:2px;font-size:8.5px;padding:8px 7px;color:var(--white)}
  .field.area{height:66px}
  .send{position:absolute;left:19px;top:209px;width:91px;height:22px;border-radius:11px;background:var(--orange);font-size:8.5px;font-weight:600;display:flex;align-items:center;justify-content:center}

  .touch{position:absolute;left:567px;top:2094px}
  .touch h3{font-family:var(--serif);font-weight:700;font-size:25px;color:var(--gold);margin-bottom:8px}
  .touch li{list-style:none;display:flex;align-items:center;gap:9px;font-size:14.5px;height:30px}
  .touch svg{width:24px;height:24px}

  .footer{position:absolute;left:0;top:2365px;width:1093px;height:40px;background:var(--white);color:var(--footer-text);font-size:10px;text-align:center;line-height:40px}
</style>
</head>
<body>
<div class="stage">
  <div class="page">

    <svg class="deco" viewBox="0 0 1093 2405" aria-hidden="true">
      <polygon points="0,0 162,0 0,90" fill="var(--sky-blue)"/>
      <polygon points="162,0 195,0 0,118 0,90" fill="var(--deep-blue)"/>
      <line x1="0" y1="128" x2="212" y2="0" stroke="var(--gold)" stroke-width="5"/>
    </svg>

    <nav class="nav">
      <a class="active">Home</a><a>About Us</a><a>Our Services</a><a>Free Estimate</a><a>Contact</a>
    </nav>

    <div class="brand"><span class="brand-dot"></span>Coral Bay Pools</div>

    <h1 class="hero-title">Crystal<br>Clear Pools, All<br>Year Round</h1>
    <p class="hero-sub">Your trusted partner for pool maintenance,<br>repair &amp; remodeling in Las Vegas.</p>
    <a class="btn hero-btn">Get a Free Quote</a>

    <svg class="deco" viewBox="0 0 1093 2405" role="img" aria-label="Photo of a luxury backyard pool with palm trees and a stone villa">
      <defs>
        <linearGradient id="heroPhoto" x1="0" y1="0" x2="0" y2="1">
          <stop offset="0" stop-color="#b9a894"/>
          <stop offset="0.45" stop-color="#8a7a62"/>
          <stop offset="0.7" stop-color="#3f5a52"/>
          <stop offset="1" stop-color="#2c3a3a"/>
        </linearGradient>
      </defs>
      <path d="M1093,172 L975,92 Q945,74 915,92 L545,333 Q515,358 545,383 L915,624 Q945,642 975,624 L1093,548" fill="none" stroke="var(--gold)" stroke-width="5"/>
      <path d="M1093,180 L970,104 Q945,90 920,104 L560,340 Q538,358 560,376 L920,612 Q945,626 970,612 L1093,540" fill="none" stroke="var(--deep-blue)" stroke-width="10"/>
      <path d="M1093,188 L968,112 Q945,100 922,112 L570,344 Q552,358 570,372 L922,604 Q945,616 968,604 L1093,532 Z" fill="url(#heroPhoto)"/>
    </svg>

    <div class="ring-word" style="top:653px"><span>O</span><span>U</span><span>R</span></div>
    <div class="ring-word" style="top:704px"><span>S</span><span>E</span><span>V</span><span>I</span><span>C</span><span>E</span><span>S</span></div>

    <div class="card" style="left:61px">
      <div class="card-icon" role="img" aria-label="Icon of a technician cleaning a pool"><i></i></div>
      <h3>Pool Cleaning</h3>
      <p>Regular cleaning to keep your pool sparkling clean &amp; hygienic for your family and friends.</p>
      <a class="btn">Learn More</a>
    </div>
    <div class="card" style="left:310px">
      <div class="card-icon" role="img" aria-label="Icon of repair tools and equipment"><i></i></div>
      <h3>Repairs &amp; Equipment</h3>
      <p>From leak detection to pump &amp; filter repairs, our technicians fix issues promptly &amp; professionally.</p>
      <a class="btn">Learn More</a>
    </div>
    <div class="card" style="left:559px">
      <div class="card-icon" role="img" aria-label="Icon of a maintenance plan document"><i></i></div>
      <h3>Maintenance Plans</h3>
      <p>Custom maintenance plans tailored to your needs for worry‑free pool ownership.</p>
      <a class="btn">Learn More</a>
    </div>
    <div class="card" style="left:808px">
      <div class="card-icon" role="img" aria-label="Icon of renovation tools"><i></i></div>
      <h3>Renovation &amp; Remodel</h3>
      <p>Transform your backyard with custom pool resurfacing, tile work &amp; modern upgrades.</p>
      <a class="btn">Learn More</a>
    </div>

    <svg class="deco" viewBox="0 0 1093 2405" role="img" aria-label="Photos of a modern home with an illuminated pool at dusk">
      <defs>
        <linearGradient id="aboutPhoto" x1="0" y1="0" x2="0" y2="1">
          <stop offset="0" stop-color="#8a9bb4"/>
          <stop offset="0.5" stop-color="#9a8470"/>
          <stop offset="1" stop-color="#23384c"/>
        </linearGradient>
        <linearGradient id="pondPhoto" x1="0" y1="0" x2="0" y2="1">
          <stop offset="0" stop-color="#8c8a84"/>
          <stop offset="1" stop-color="#1f3a44"/>
        </linearGradient>
      </defs>
      <path d="M0,1160 L62,1126 Q80,1116 98,1126 L400,1313 Q428,1340 400,1366 L170,1518" fill="none" stroke="var(--gold)" stroke-width="5"/>
      <path d="M0,1172 L66,1136 Q80,1128 94,1136 L390,1320 Q412,1340 390,1360 L155,1518" fill="none" stroke="var(--deep-blue)" stroke-width="9"/>
      <path d="M0,1184 L70,1144 Q80,1138 90,1144 L382,1326 Q398,1340 382,1354 L145,1518 L0,1518 Z" fill="url(#aboutPhoto)"/>
      <path d="M205,1518 L462,1367 Q485,1352 508,1367 L740,1518" fill="none" stroke="var(--gold)" stroke-width="5"/>
      <path d="M222,1518 L468,1376 Q485,1366 502,1376 L725,1518" fill="none" stroke="var(--deep-blue)" stroke-width="9"/>
      <path d="M235,1518 L472,1383 Q485,1376 498,1383 L712,1518 Z" fill="url(#pondPhoto)"/>
    </svg>

    <h2 class="about-head"><span class="small">About</span><br><span class="big">Coral Bay Pools LV</span></h2>
    <p class="about-text">Coral Bay Pools LV is a family‑owned and operated pool service and repair company serving Las Vegas and surrounding areas. With over a decade of experience, we are dedicated to providing reliable, top‑quality pool care so you can enjoy your backyard oasis year round. We take pride in our attention to detail, friendly customer service, and deep knowledge of pool systems. Whether you need weekly cleaning, urgent repairs or a complete pool renovation, our certified technicians are here to help.</p>
    <a class="btn about-btn">Learn More</a>

    <section class="band">
      <h2>Relax, We’ve Got Your Pool Covered</h2>
      <p>Let our experts keep your pool safe, clean &amp; ready for every occasion.</p>
      <a class="band-btn">Schedule Service</a>
    </section>

    <div class="ring-word" style="top:1860px"><span>C</span><span>O</span><span>N</span><span>T</span><span>A</span><span>C</span><span>T</span></div>
    <div class="ring-word" style="top:1907px"><span>U</span><span>S</span></div>
    <p class="contact-intro">Ready to make a splash? Send us a message or give us a call<br>and we’ll get back to you as soon as possible.</p>

    <form class="form">
      <div class="field" style="top:19px">Your Name</div>
      <div class="field" style="top:56px">Email Address</div>
      <div class="field" style="top:93px">Phone Number</div>
      <div class="field area" style="top:130px">How can we help you?</div>
      <div class="send">Send Message</div>
    </form>

    <svg class="deco" viewBox="0 0 1093 2405" role="img" aria-label="Photo of a lit backyard pool and patio at night">
      <defs>
        <linearGradient id="nightPhoto" x1="0" y1="0" x2="0" y2="1">
          <stop offset="0" stop-color="#4a6fb0"/>
          <stop offset="0.5" stop-color="#6a6a78"/>
          <stop offset="1" stop-color="#1c3558"/>
        </linearGradient>
      </defs>
      <path d="M790,2405 L700,2345 Q680,2325 700,2305 L1010,2116 Q1050,2095 1093,2120" fill="none" stroke="var(--gold)" stroke-width="5"/>
      <path d="M805,2405 L712,2342 Q696,2325 712,2310 L1015,2128 Q1050,2110 1093,2132" fill="none" stroke="var(--deep-blue)" stroke-width="9"/>
      <path d="M818,2405 L722,2340 Q708,2325 722,2314 L1020,2138 Q1052,2122 1093,2142 L1093,2405 Z" fill="url(#nightPhoto)"/>
    </svg>

    <div class="touch">
      <h3>Get in Touch</h3>
      <ul>
        <li><svg viewBox="0 0 24 24" aria-hidden="true"><circle cx="12" cy="12" r="11" fill="none" stroke="var(--gold)" stroke-width="1.5"/><path d="M8.5 6.5h3l1 3-1.6 1a6 6 0 0 0 2.6 2.6l1-1.6 3 1v3a1 1 0 0 1-1 1A10 10 0 0 1 7.5 7.5a1 1 0 0 1 1-1z" fill="none" stroke="#fff" stroke-width="1.2"/></svg>(702) 555-0147</li>
        <li><svg viewBox="0 0 24 24" aria-hidden="true"><circle cx="12" cy="12" r="11" fill="none" stroke="var(--gold)" stroke-width="1.5"/><rect x="6.5" y="8" width="11" height="8" rx="1" fill="none" stroke="#fff" stroke-width="1.2"/><path d="M6.5 8.5 12 12.5l5.5-4" fill="none" stroke="#fff" stroke-width="1.2"/></svg>info@coralbaypoolslv.com</li>
        <li><svg viewBox="0 0 24 24" aria-hidden="true"><circle cx="12" cy="12" r="11" fill="none" stroke="var(--gold)" stroke-width="1.5"/><path d="M12 18s-4.5-4.3-4.5-7.5a4.5 4.5 0 0 1 9 0C16.5 13.7 12 18 12 18z" fill="none" stroke="#fff" stroke-width="1.2"/><circle cx="12" cy="10.5" r="1.6" fill="none" stroke="#fff" stroke-width="1.2"/></svg>Las Vegas, NV</li>
      </ul>
    </div>

    <footer class="footer">© 2026 Coral Bay Pools LV. All rights reserved.</footer>
  </div>
</div>
</body>
</html>
```